New Business Card for our Indoor Golf Training Facility

We are looking for designs for a new business card for our indoor golf training facility. Attached is our logo, our logo with our slogan, and here is our elevator pitch (What makes us different from the others) not sure if all the info will fit on one card, maybe you can condense the elevator pitch? here is the info

Elevator Pitch
We work with serious golfers and those that want to be serious golfers…
to make you better, faster, at all phases of the game…
We use the same state-of-the-art technology as professional golfers…
which produces data sets that shows your improvement in real time.
Our facility is available 24/7 to our members, which allows you to improve on your time.

our website: www.birchpinlinks.com

Target Market(s)

Golfers

Font styles to use
Serif
Sans Serif

Colors
ec1f27
f59195
fbd4d5
919191
d3d3d3
1b1b1b

Requirements
Must have
• our logo or our logo with the slogan, elevator pitch (can be condensed or shortened)

```html
<!DOCTYPE html>
<html lang="en">
<head>
<meta charset="utf-8">
<title>Birch Pin Links – Business Card</title>
<link rel="stylesheet" href="https://fonts.googleapis.com/css2?family=Roboto:wght@400;500;700&family=Roboto+Condensed:wght@400;700&display=swap">
<style>
  :root {
    --brand-red: #ec3f37;
    --ink: #1b1b1b;
    --ink-soft: #4a4a4a;
    --rule: #919191;
    --card-white: #f2f2f2;
    --backdrop: #2e2e2e;
    --white: #ffffff;
  }
  * { margin: 0; padding: 0; box-sizing: border-box; }
  html, body { width: 1200px; height: 960px; overflow: hidden; }
  body {
    background: var(--backdrop);
    font-family: "Roboto", Arial, sans-serif;
    position: relative;
  }
  .card {
    position: absolute;
    width: 600px;
    height: 342px;
    border-radius: 20px;
  }
  .card--front { left: 322px; top: 110px; background: var(--card-white); }
  .card--back { left: 320px; top: 494px; background: var(--brand-red); color: var(--white); text-align: center; }

  .brand {
    position: absolute;
    left: 54px;
    top: 138px;
  }
  .brand__row { display: flex; align-items: center; gap: 8px; }
  .brand__dot {
    width: 46px; height: 46px; border-radius: 50%;
    border: 3px solid var(--brand-red);
  }
  .brand__name {
    color: var(--brand-red);
    font-weight: 700;
    font-size: 27px;
    letter-spacing: -0.3px;
  }
  .brand__tagline {
    color: var(--brand-red);
    font-size: 11px;
    margin: 2px 0 0 55px;
  }

  .divider {
    position: absolute;
    left: 326px; top: 88px;
    width: 1px; height: 158px;
    background: linear-gradient(to bottom, transparent, var(--rule) 20%, var(--rule) 80%, transparent);
  }

  .contact {
    position: absolute;
    left: 352px; top: 86px;
  }
  .contact__name { color: var(--brand-red); font-weight: 700; font-size: 22px; line-height: 1.1; }
  .contact__role { color: var(--ink); font-weight: 500; font-size: 15px; margin-top: 2px; }
  .contact__address { color: var(--ink-soft); font-size: 15px; line-height: 19px; margin-top: 8px; }
  .contact__list { list-style: none; margin-top: 8px; }
  .contact__item {
    display: flex; align-items: center; gap: 9px;
    color: var(--ink-soft); font-size: 15px; line-height: 19.5px;
  }
  .contact__icon { width: 13px; height: 13px; fill: var(--brand-red); flex: none; }

  .emblem {
    width: 74px; height: 74px; border-radius: 50%;
    border: 6px solid var(--white);
    margin: 36px auto 0;
  }
  .back__brand { font-weight: 700; font-size: 20px; line-height: 24px; margin-top: 8px; }
  .pitch__title { font-weight: 700; font-size: 19px; line-height: 22px; margin-top: 30px; }
  .pitch__text {
    font-family: "Roboto Condensed", Arial, sans-serif;
    font-size: 14.5px; line-height: 18px; margin-top: 6px;
  }
  .social { display: flex; justify-content: center; gap: 4px; margin-top: 10px; }
  .social__dot { width: 18px; height: 18px; border-radius: 50%; background: var(--white); }
</style>
</head>
<body>

<section class="card card--front">
  <div class="brand">
    <div class="brand__row">
      <span class="brand__dot"></span>
      <span class="brand__name">Birch Pin Links</span>
    </div>
    <p class="brand__tagline">Train Smarter. Play Sharper. Every Day.</p>
  </div>

  <div class="divider"></div>

  <div class="contact">
    <p class="contact__name">DANIEL MARSH</p>
    <p class="contact__role">CEO/FOUNDER</p>
    <p class="contact__address">1480 W. Alder Rd. Unit B4<br>Lakewood Falls, OH 45390</p>
    <ul class="contact__list">
      <li class="contact__item">
        <svg class="contact__icon" viewBox="0 0 24 24"><path d="M6.6 10.8a15.1 15.1 0 0 0 6.6 6.6l2.2-2.2a1 1 0 0 1 1-.25 11.4 11.4 0 0 0 3.6.57 1 1 0 0 1 1 1V20a1 1 0 0 1-1 1A17 17 0 0 1 3 4a1 1 0 0 1 1-1h3.5a1 1 0 0 1 1 1c0 1.25.2 2.45.57 3.57a1 1 0 0 1-.25 1z"/></svg>
        555-210-3387
      </li>
      <li class="contact__item">
        <svg class="contact__icon" viewBox="0 0 24 24"><path d="M2 5h20v14H2z M3 6l9 7 9-7" stroke="#f2f2f2" stroke-width="1.6"/></svg>
        info@birchpinlinks.com
      </li>
      <li class="contact__item">
        <svg class="contact__icon" viewBox="0 0 24 24"><circle cx="12" cy="12" r="10"/><path d="M2 12h20M12 2c3 3 3 17 0 20M12 2c-3 3-3 17 0 20" stroke="#f2f2f2" stroke-width="1.4" fill="none"/></svg>
        birchpinlinks.com
      </li>
    </ul>
  </div>
</section>

<section class="card card--back">
  <div class="emblem"></div>
  <p class="back__brand">Birch Pin Links</p>
  <h2 class="pitch__title">ELEVATOR PITCH :</h2>
  <p class="pitch__text">
    We work with serious golfers and those that want to be serious golfers…<br>
    to make you better, faster, at all phases of the game…<br>
    We use the same state-of-the-art technology as professional golfers…<br>
    which produces data sets that shows your improvement in real time.<br>
    Our facility is available 24/7 to our members, which allows you to improve on your time.
  </p>
  <div class="social">
    <span class="social__dot"></span>
    <span class="social__dot"></span>
  </div>
</section>

</body>
</html>
```